FLOWr PI Planning Web App - Lean Agile at Scale - Distributed Big Room Planning Web & Touchscr...

We are the provider of the boardwise app http://boardwise-demo.test which currently is a desktop application. We are now working to bring all the features to a web-app but we don’t have a catchy design yet. The boardwise app is a visual collaboration tool for globally distributed teams and organization. Imagine a wall with lots of sticky notes on a flipchart hanging there – that’s basically our app just in a digital format. In general we want a light, modern, state of the art look and feel. Please take colorblind people into consideration when designing it.We are specifically looking for the following two design parts:- Design of the board structure- Sticky note designRequirements for the board structure- 16:9 ratio fixed- The board can be structured in 2 to 12 iterations + Risk Area and Objectives. Most common is 5 iterations + Risk Area and Objectives. Please go with the most common one but have in the back of your head that it needs to be compatible with 14 sections. Just for your imagination: in real life each of these areas on the board is one flip chart page.- Team Name: Somewhere on the board has to be the team name. It has to be easy to find and read.- In the iteration fields the user can set a velocity. That’s a simple numbers field. The load is calculated automatically and is just a number displayed on the board. There is an automatic visual indicator which should show with green or red colors if the teams are still in the plan. How this is brought to the attention is up to you.- Objectives & Stretch Objectives: The area with the Objectives is a list with text and a prioritization number attached to it. BV on the sketch stands for Business Value.Sticky Note design descriptionThe Sticky Note represents a physical sticky note or post-it note. When the user sees it he should instantly understand it as a sticky note and so for intuitively know what to do with it.Unselected sticky noteIf the sticky note is not selected it should be a simple sticky note sitting on the board.Following you find the things visible when the sticky note is not selected:- The sticky notes have a squared form factor- There is the text which is on the sticky note- In the upper right corner is a small sticky ID. Something like e.g. QX-7816.- Somewhere on the sticky note is also a number which should be easy to read. The numbers range from nothing over 0.5, 1, 2, 3, 5, 8, 13, 20, 40 up to 100.- Somewhere on the sticky needs to be a permanent text label. Not bigger than the rest of the text on the sticky note but easy to read.Selected sticky noteIf the user clicks on the sticky note once the following information needs to be displayed and he needs to be able to do the things listed and described below:- The sticky notes have a squared form factor- The user can write text on it- He can select different colors. These colors need to have a label so he knows what the function of these colors are.- By clicking a button he can add a flag to the sticky note- He can open a selection to choose the following number displayed on the sticky: 0.5, 1, 2, 3, 5, 8, 13, 20, 40, 100.- There is a delete sticky button. Place it where it makes sense from an intuitive stand point.- If he clicks the delete button, a short dialog appears on the sticky note: “Are you sure you want to delete this sticky note permanently? (It might delete an issue in your ALM tool)” He can confirm that by pressing “Delete” or “Cancel”.- In the upper right corner is a small sticky ID. Something like e.g. QX-7816.- Somewhere on or next to the sticky note needs to be a “sticky mirror” button as well as a “sticky move” button. Beside an optional icon for “mirror” and “move” there needs to be a naming tag so that everyone understands it right away.- It’s up to you to decide what’s the most intuitive way for the user.For better understanding also take a look at the rough sketch attached.

Font styles to use
Sans Serif

Requirements
Must have
• Color blind mode for different colored sticky notes

```html
<!DOCTYPE html>
<html lang="en">
<head>
<meta charset="utf-8">
<title>Team Board – PI Planning</title>
<link rel="stylesheet" href="https://fonts.googleapis.com/css2?family=Arimo:wght@400;700&family=Courier+Prime&display=swap">
<style>
:root{
  --green:#0cb40c;
  --green-dark:#0a6b1e;
  --bar-grey:#6b6b6b;
  --navy:#0b2a55;
  --tab-black:#1d1d1d;
  --white:#ffffff;
  --red:#ed1c24;
  --yellow:#dff22e;
  --grey-note:#c9c9c9;
  --tab-blue:#1a6fa0;
  --tab-green:#3cb64a;
  --tab-red:#ed1c24;
  --teal:#1a9bb0;
  --wall-1:#2f4f74;
  --wall-2:#b9a27a;
  --wall-3:#e4b64a;
}
*{box-sizing:border-box;margin:0;padding:0}
html,body{width:1200px;height:675px;overflow:hidden}
body{font-family:"Arimo",Arial,sans-serif;position:relative;background:var(--wall-2)}
.wall{position:absolute;inset:0;background:linear-gradient(100deg,var(--wall-1) 0%,#3f6a86 22%,#8fa6a0 38%,var(--wall-2) 55%,var(--wall-3) 72%,#d9a83c 100%)}
.top-line{position:absolute;left:0;top:0;width:1200px;height:10px;background:var(--green)}
.team-bar{position:absolute;left:0;top:10px;width:1200px;height:30px;background:var(--bar-grey)}
.team-bar::before{content:"";position:absolute;left:0;top:0;width:30px;height:30px;background:var(--green);clip-path:polygon(0 0,100% 0,0 100%)}
.team-name{position:absolute;left:34px;top:7px;color:var(--white);font-weight:700;font-size:14px;letter-spacing:.5px}

.side-panel{position:absolute;left:34px;width:172px;background:var(--white)}
.objectives{top:74px;height:358px}
.risks{top:458px;height:174px}
.panel-head{height:25px;border-radius:8px 8px 0 0;color:var(--white);font-weight:700;display:flex;align-items:center;justify-content:space-between;padding:0 12px}
.objectives .panel-head{background:var(--green-dark);font-size:10px;letter-spacing:.6px}
.risks .panel-head{background:var(--red);justify-content:center;font-size:13px;letter-spacing:.8px;height:26px}
.risks .panel-band{height:21px;background:var(--navy)}
.objective-row{position:absolute;left:0;width:172px;height:20px;background:var(--navy);color:var(--white);display:flex;align-items:center;justify-content:space-between;padding:0 19px 0 10px;font-family:"Courier Prime","Courier New",monospace;font-size:12px;letter-spacing:.6px}
.objective-row .bv{font-family:"Arimo",Arial,sans-serif;font-weight:700;font-size:9px}
.row-main{top:28px}
.row-stretch{top:188px}

.iteration{position:absolute;width:273px}
.iteration-tab{height:17px;width:110px;background:var(--tab-black);border-radius:0 12px 0 0;color:var(--white);font-size:12.5px;letter-spacing:.6px;padding:1px 0 0 9px}
.iteration-bar{height:17px;background:var(--navy);color:var(--white);font-weight:700;font-size:12px;letter-spacing:.6px;display:flex;justify-content:flex-end;align-items:center;gap:34px;padding-right:14px}
.iteration-body{position:relative;background:var(--white);height:227px}
.row-b .iteration-body{height:228px}

.sticky{position:absolute;width:64px}
.sticky-tab{height:8px;border-radius:6px 6px 0 0;background:var(--tab-black);color:var(--white);font-size:6px;line-height:8px;text-align:right;padding-right:4px;letter-spacing:.2px}
.sticky-body{height:55px;box-shadow:1px 3px 4px rgba(0,0,0,.45)}
.tab-blue .sticky-tab{background:var(--tab-blue)}
.tab-green .sticky-tab{background:var(--tab-green)}
.tab-red .sticky-tab{background:var(--tab-red)}
.note-red .sticky-body{background:var(--red)}
.note-yellow .sticky-body{background:var(--yellow)}
.note-grey .sticky-body{background:var(--grey-note)}
.selected .sticky-body{box-shadow:0 5px 7px rgba(230,20,140,.7)}

.note-menu{position:absolute;list-style:none}
.note-menu li{display:flex;align-items:center;gap:4px;height:22px;font-size:5.5px;color:#222}
.note-menu .dot{width:14px;height:14px;border-radius:50%;background:var(--teal);display:inline-block}

.action{position:absolute;text-align:center}
.action-label{position:absolute;left:50%;transform:translateX(-50%);font-size:18px;letter-spacing:1.2px;color:#1a1a1a;white-space:nowrap}
.action-btn{border-radius:50%;display:flex;align-items:center;justify-content:center}
.act-move{left:1124px;top:450px}
.act-move .action-btn{width:72px;height:72px;background:var(--green-dark)}
.act-move .action-label{top:-23px}
.act-mirror{left:1038px;top:502px}
.act-mirror .action-btn{width:72px;height:72px;background:#050505}
.act-mirror .action-label{top:-27px}
.act-delete{left:975px;top:591px}
.act-delete .action-btn{width:74px;height:74px;background:var(--red)}
.act-delete .action-label{top:-25px;left:34px}
</style>
</head>
<body>
<div class="wall" role="img" aria-label="Painted brick wall with graffiti in blue, teal and yellow as board background"></div>

<header class="top-line"></header>
<div class="team-bar"><span class="team-name">TEAM NY</span></div>

<section class="side-panel objectives">
  <div class="panel-head"><span>OBJECTIVES</span><span>BV</span></div>
  <div class="objective-row row-main"><span>My Objective</span><span class="bv">15</span></div>
  <div class="objective-row row-stretch"><span>My Stretch</span><span class="bv">5</span></div>
</section>

<section class="side-panel risks">
  <div class="panel-head">RISKS</div>
  <div class="panel-band"></div>
</section>

<section class="iteration" style="left:262px;top:77px">
  <div class="iteration-tab">iteration 1.1</div>
  <div class="iteration-bar"><span>velocity 20</span><span>Load&nbsp;&nbsp;5</span></div>
  <div class="iteration-body">
    <div class="sticky note-grey" style="left:33px;top:18px"><div class="sticky-tab">QX 7816</div><div class="sticky-body"></div></div>
    <div class="sticky note-red" style="left:135px;top:18px"><div class="sticky-tab">QX 7816</div><div class="sticky-body"></div></div>
    <div class="sticky note-yellow" style="left:32px;top:114px"><div class="sticky-tab">QX 7816</div><div class="sticky-body"></div></div>
    <div class="sticky note-red tab-blue" style="left:194px;top:132px"><div class="sticky-tab">QX 7816</div><div class="sticky-body"></div></div>
  </div>
</section>

<section class="iteration" style="left:558px;top:77px">
  <div class="iteration-tab">iteration 1.1</div>
  <div class="iteration-bar"><span>velocity 20</span><span>Load&nbsp;&nbsp;5</span></div>
  <div class="iteration-body">
    <div class="sticky note-grey tab-blue" style="left:74px;top:44px"><div class="sticky-tab">QX 7816</div><div class="sticky-body"></div></div>
    <div class="sticky note-red" style="left:178px;top:18px"><div class="sticky-tab">QX 7816</div><div class="sticky-body"></div></div>
    <div class="sticky note-yellow" style="left:15px;top:135px"><div class="sticky-tab">QX 7816</div><div class="sticky-body"></div></div>
    <div class="sticky note-red selected" style="left:108px;top:135px"><div class="sticky-tab">QX 7816</div><div class="sticky-body"></div></div>
    <ul class="note-menu" style="left:192px;top:138px">
      <li><span class="dot"></span>Delete</li>
      <li><span class="dot"></span>Mirror</li>
      <li><span class="dot"></span>Move</li>
    </ul>
  </div>
</section>

<section class="iteration" style="left:855px;top:77px">
  <div class="iteration-tab">iteration 1.1</div>
  <div class="iteration-bar"><span>velocity 20</span><span>Load&nbsp;&nbsp;5</span></div>
  <div class="iteration-body">
    <div class="sticky note-yellow tab-green" style="left:32px;top:18px"><div class="sticky-tab">QX 7816</div><div class="sticky-body"></div></div>
    <div class="sticky note-grey tab-blue" style="left:190px;top:18px"><div class="sticky-tab">QX 7816</div><div class="sticky-body"></div></div>
    <div class="sticky note-grey" style="left:30px;top:138px"><div class="sticky-tab">QX 7816</div><div class="sticky-body"></div></div>
    <div class="sticky note-red tab-green" style="left:119px;top:135px"><div class="sticky-tab">QX 7816</div><div class="sticky-body"></div></div>
  </div>
</section>

<section class="iteration row-b" style="left:262px;top:370px">
  <div class="iteration-tab">iteration 1.1</div>
  <div class="iteration-bar"><span>velocity 20</span><span>Load&nbsp;&nbsp;5</span></div>
  <div class="iteration-body">
    <div class="sticky note-yellow tab-blue" style="left:22px;top:10px"><div class="sticky-tab">QX 7816</div><div class="sticky-body"></div></div>
    <div class="sticky note-grey tab-red" style="left:117px;top:38px"><div class="sticky-tab">QX 7816</div><div class="sticky-body"></div></div>
    <div class="sticky note-yellow tab-blue" style="left:64px;top:151px"><div class="sticky-tab">QX 7816</div><div class="sticky-body"></div></div>
    <div class="sticky note-grey" style="left:198px;top:141px"><div class="sticky-tab">QX 7816</div><div class="sticky-body"></div></div>
  </div>
</section>

<section class="iteration row-b" style="left:562px;top:370px">
  <div class="iteration-tab">iteration 1.1</div>
  <div class="iteration-bar"><span>velocity 20</span><span>Load&nbsp;&nbsp;5</span></div>
  <div class="iteration-body">
    <div class="sticky note-grey" style="left:12px;top:38px"><div class="sticky-tab">QX 7816</div><div class="sticky-body"></div></div>
    <div class="sticky note-yellow tab-blue" style="left:165px;top:62px"><div class="sticky-tab">QX 7816</div><div class="sticky-body"></div></div>
    <div class="sticky note-red" style="left:105px;top:140px"><div class="sticky-tab">QX 7816</div><div class="sticky-body"></div></div>
  </div>
</section>

<div class="action act-move">
  <span class="action-label">Move</span>
  <div class="action-btn">
    <svg width="44" height="36" viewBox="0 0 44 36" aria-hidden="true">
      <rect x="4" y="2" width="24" height="32" fill="#fff"/>
      <g stroke="#0a6b1e" stroke-width="2"><line x1="8" y1="9" x2="24" y2="9"/><line x1="8" y1="14" x2="24" y2="14"/><line x1="8" y1="19" x2="24" y2="19"/><line x1="8" y1="24" x2="24" y2="24"/><line x1="8" y1="29" x2="24" y2="29"/></g>
      <path d="M31 18h10M37 13l5 5-5 5" stroke="#fff" stroke-width="3" fill="none"/>
    </svg>
  </div>
</div>

<div class="action act-mirror">
  <span class="action-label">Mirror</span>
  <div class="action-btn">
    <svg width="54" height="30" viewBox="0 0 54 30" aria-hidden="true">
      <rect x="2" y="3" width="18" height="24" fill="#fff"/>
      <rect x="34" y="3" width="18" height="24" fill="#fff"/>
      <g stroke="#050505" stroke-width="1.6"><line x1="5" y1="9" x2="17" y2="9"/><line x1="5" y1="14" x2="17" y2="14"/><line x1="5" y1="19" x2="17" y2="19"/><line x1="37" y1="9" x2="49" y2="9"/><line x1="37" y1="14" x2="49" y2="14"/><line x1="37" y1="19" x2="49" y2="19"/></g>
      <path d="M23 15h8M28 11l4 4-4 4" stroke="#fff" stroke-width="2.5" fill="none"/>
    </svg>
  </div>
</div>

<div class="action act-delete">
  <span class="action-label">Delete</span>
  <div class="action-btn">
    <svg width="30" height="36" viewBox="0 0 30 36" aria-hidden="true">
      <path d="M4 6h22l-2 4H6z" fill="#fff"/>
      <rect x="10" y="1" width="10" height="4" fill="#fff"/>
      <path d="M6 12h18l-2.5 22h-13z" fill="#fff"/>
    </svg>
  </div>
</div>
</body>
</html>
```